Webdesign für Hersteller für Pack- und Palettieranlagen für den Getränke- und Lebensmittelbereich
Webdesign für Hersteller für Pack- und Palettieranlagen für den Getränke- und Lebensmittelbere..
Zielgruppe
Hersteller für Pack- und Palettieranlagen für den Getränke- und Lebensmittelbereich
Zielgruppe: Getränke- und Lebensmittelhersteller
Aufgabenstellung
die zukünftige Seite soll dynamischer und intuitiver werden
klare Strukturen, aber morderner als das jetztige Layout
Keine Kopie der alten Seite www.kolmatech.de!
Startseite soll aufgeräumter sein
Logo, Rufnummer, Mail, Social Media
Startseite mit großem Headerbild (Slider)

```html
<!DOCTYPE html>
<html lang="de">
<head>
<meta charset="utf-8">
<title>KOLMA Maschinenbau GmbH</title>
<link href="https://fonts.googleapis.com/css2?family=Inter:wght@400;500;600;700;800&display=swap" rel="stylesheet">
<style>
:root{
  --green:#6ab42d;
  --green-light:#7cc33f;
  --dark:#4a4a4a;
  --darker:#3a3a3a;
  --orange:#f07d1a;
  --light:#f2f2f2;
  --text:#444;
  --white:#fff;
}
*{box-sizing:border-box;margin:0;padding:0}
html,body{width:1200px;height:3477px;overflow:hidden}
body{font-family:'Inter',sans-serif;color:var(--text);position:relative;background:var(--white)}
.abs{position:absolute}
.topbar{left:0;top:0;width:1200px;height:38px;background:var(--green);color:var(--white);font-size:13px;display:flex;align-items:center;padding:0 74px}
.topbar .item{display:flex;align-items:center;gap:10px;margin-right:36px}
.topbar .social{margin-left:auto;display:flex;gap:12px}
.topbar .social span{width:14px;height:14px;border-radius:50%;background:var(--white);display:block}
.nav{left:0;top:38px;width:1200px;height:55px;background:var(--dark)}
.nav .brand{position:absolute;left:0;top:0;width:243px;height:55px;background:var(--white);clip-path:polygon(0 0,210px 0,243px 55px,0 55px);display:flex;align-items:center;padding-left:74px}
.brand .name{font-weight:700;font-size:19px;color:var(--dark);line-height:1;letter-spacing:.5px}
.nav ul{position:absolute;left:265px;top:0;height:55px;display:flex;align-items:center;gap:18px;list-style:none;color:var(--white);font-size:11.5px;font-weight:600}
.hero{left:0;top:93px;width:1200px;height:519px;background:linear-gradient(135deg,#6d5a46 0%,#3f4a5e 45%,#7a6a4c 75%,#2f3848 100%)}
.hero-shade{left:0;top:93px;width:1200px;height:519px;background:linear-gradient(90deg,rgba(0,0,0,.45),rgba(0,0,0,.05))}
.hero h1{left:74px;top:164px;width:600px;color:var(--white);font-size:45px;font-weight:800;line-height:1;letter-spacing:-.3px}
.hero-sub{left:74px;top:378px;width:420px;color:var(--white);font-size:11px;font-weight:600;line-height:1.05}
.btn{display:flex;align-items:center;justify-content:center;color:var(--white);font-weight:700;font-size:13px;box-shadow:0 3px 6px rgba(0,0,0,.25)}
.btn-green{background:var(--green)}
.btn-dark{background:var(--dark)}
.hero .btn{left:74px;top:472px;width:145px;height:37px}
.dots{left:570px;top:586px;display:flex;gap:9px}
.dots span{width:8px;height:8px;background:var(--white)}
.dots span.on{background:transparent;border:1.5px solid var(--white)}
.section-title{position:absolute;left:0;width:1200px;text-align:center;font-size:25px;font-weight:700;color:var(--dark)}
.section-title::after{content:"";display:block;width:172px;height:2px;background:var(--green);margin:9px auto 0}
.produkte{left:0;top:612px;width:1200px;height:1004px;background:var(--light)}
.tile{position:absolute;width:519px;height:374px;overflow:hidden;box-shadow:0 6px 16px rgba(0,0,0,.12)}
.tile .photo{position:absolute;inset:0}
.tile .band{position:absolute;left:0;top:146px;width:100%;height:78px;background:rgba(74,74,74,.95);display:flex;align-items:center;justify-content:center;color:var(--green-light);font-size:35px;font-weight:800}
.tile.active .photo::after{content:"";position:absolute;inset:0;background:rgba(106,180,45,.85)}
.tile.active .title{position:absolute;top:160px;width:100%;text-align:center;color:var(--white);font-size:35px;font-weight:800}
.tile.active .more{position:absolute;top:290px;width:100%;text-align:center;color:var(--white);font-size:13px;font-weight:600}
.aktuelles{left:0;top:1616px;width:1200px;height:591px;background:var(--white)}
.aktuelles .section-title::after{background:var(--orange)}
.slide{position:absolute;top:142px;height:375px}
.slide-main .cap{position:absolute;left:42px;top:230px;width:440px;color:var(--white)}
.slide-main h3{font-size:28px;font-weight:800;line-height:1}
.slide-main p{font-size:11px;line-height:1.05;margin-top:14px}
.arrow{position:absolute;top:320px}
.jobs{left:0;top:2207px;width:1200px;height:315px;background:var(--green)}
.jobs h2{position:absolute;top:49px;width:100%;text-align:center;color:var(--white);font-size:25px;font-weight:700}
.job{position:absolute;top:118px;width:253px;height:155px;background:var(--white);text-align:center;padding-top:20px;box-shadow:0 3px 8px rgba(0,0,0,.15)}
.job h4{font-size:15px;font-weight:600;color:var(--dark)}
.job p{font-size:8.5px;line-height:1.05;width:170px;margin:12px auto 0;color:#666}
.job .btn{width:143px;height:36px;margin:16px auto 0}
.person{left:1026px;top:2183px;width:174px;height:339px;background:linear-gradient(180deg,#e9e9e9 0%,#c9c2b8 40%,#7b8591 100%);border-radius:80px 80px 0 0}
.unternehmen{left:0;top:2522px;width:1200px;height:376px;background:linear-gradient(180deg,#fff 0%,#eaeaea 45%,#d7d7d7 100%)}
.unternehmen .logo-big{position:absolute;left:120px;top:170px;font-size:30px;font-weight:700;color:var(--dark);line-height:1}
.unternehmen .copy{position:absolute;left:606px;top:135px;width:512px;font-size:11px;line-height:1.05;color:#555}
.unternehmen .copy p+p{margin-top:10px}
.unternehmen .btn{position:absolute;left:606px;top:279px;width:143px;height:36px}
.kontakt{left:0;top:2898px;width:606px;height:412px;background:var(--white)}
.kontakt h2{position:absolute;left:74px;top:58px;font-size:25px;font-weight:700;color:var(--dark)}
.field{position:absolute;width:175px}
.field label{display:block;font-size:11px;color:#333;margin-bottom:4px}
.field .input{height:24px;background:#eee;font-size:10.5px;color:#aaa;padding:6px 8px}
.field .input.filled{color:#333}
.building{left:606px;top:2898px;width:594px;height:412px;background:linear-gradient(160deg,#f2f4f6 0%,#c8d0d8 45%,#5d6b7a 80%,#9aa4ad 100%)}
.footer{left:0;top:3310px;width:1200px;height:167px;background:var(--darker);color:#ddd;font-size:9.5px}
.footer h5{font-size:10.5px;font-weight:700;color:var(--white);margin-bottom:12px}
.fcol{position:absolute;top:30px;line-height:2.1}
.copyright{position:absolute;left:0;bottom:0;width:100%;height:34px;border-top:1px solid #555;text-align:center;line-height:34px;font-size:9.5px}
</style>
</head>
<body>

<div class="abs topbar">
  <div class="item"><svg width="12" height="12" viewBox="0 0 24 24"><path fill="#fff" d="M6.6 10.8a15 15 0 0 0 6.6 6.6l2.2-2.2c.3-.3.7-.4 1-.2 1.1.4 2.3.6 3.6.6.6 0 1 .4 1 1V20c0 .6-.4 1-1 1A17 17 0 0 1 3 4c0-.6.4-1 1-1h3.5c.6 0 1 .4 1 1 0 1.3.2 2.5.6 3.6.1.3 0 .7-.2 1z"/></svg>030 / 4567 - 0</div>
  <div class="item"><svg width="12" height="10" viewBox="0 0 24 18"><path fill="#fff" d="M0 0h24v18H0zM12 10 1 2v1l11 8 11-8V2z"/></svg>info@kolmatech.de</div>
  <div class="social"><span></span><span></span><span></span><span></span></div>
</div>

<div class="abs nav">
  <div class="brand"><span class="name">KOLMA</span></div>
  <ul><li>UNTERNEHMEN</li><li>JOBS / KARRIERE</li><li>PALETTIERTECHNIK</li><li>PACKERTECHNIK</li><li>FÖRDERTECHNIK</li><li>ANLAGEN</li><li>GEBRAUCHTMASCHINEN</li><li>AKTUELLES</li></ul>
</div>

<div class="abs hero" role="img" aria-label="Foto einer großen Produktionshalle mit Förderanlagen"></div>
<div class="abs hero-shade"></div>
<div class="hero">
  <h1 class="abs">Hersteller Für Pack-<br>Und Palettieranlagen<br>Für Den Getränke-<br>Und Lebensmittelbereich</h1>
  <p class="abs hero-sub">Lorem Ipsum Dolor Sit Amet, Consectetur Adipiscing Elit, Sed Do Eiusmod Tempor Incididunt Ut Labore Et Dolore Magna Aliqua. Ut Enim Ad Minim Veniam, Quis Nostrud Exercitation Ullamco Laboris Nisi Ut Aliquip Ex Ea Commodo Consequat.</p>
  <div class="abs btn btn-green">Mehr Erfahren</div>
  <div class="abs dots"><span class="on"></span><span></span><span></span><span></span></div>
</div>

<section class="abs produkte">
  <h2 class="section-title" style="top:48px">PRODUKTE</h2>
  <div class="tile" style="left:74px;top:133px">
    <div class="photo" role="img" aria-label="Foto einer gelben Palettieranlage" style="background:linear-gradient(160deg,#d8d8d0,#c9a93a 45%,#4d5660)"></div>
    <div class="band">PALETTIERTECHNIK</div>
  </div>
  <div class="tile active" style="left:606px;top:133px">
    <div class="photo" role="img" aria-label="Foto einer Packanlage" style="background:linear-gradient(160deg,#cfd8c0,#8aa070)"></div>
    <div class="title">PACKERTECHNIK</div>
    <div class="more">Mehr Erfahren &nbsp;›</div>
  </div>
  <div class="tile" style="left:74px;top:521px">
    <div class="photo" role="img" aria-label="Foto von Flaschen auf einem Förderband" style="background:linear-gradient(160deg,#e4e8ea,#8a8e90 50%,#a23a2a 80%,#6a3020)"></div>
    <div class="band">FÖRDERTECHNIK</div>
  </div>
  <div class="tile" style="left:606px;top:521px">
    <div class="photo" role="img" aria-label="Foto gebrauchter Maschinen und Getränkekisten" style="background:linear-gradient(160deg,#b0a090,#8a6a4a 45%,#2a2a2a 75%,#c8c8c8)"></div>
    <div class="band">GEBRAUCHTMASCHINEN</div>
  </div>
</section>

<section class="abs aktuelles">
  <h2 class="section-title" style="top:52px">AKTUELLES</h2>
  <div class="slide" role="img" aria-label="Foto einer Roboteranlage" style="left:0;width:239px;background:linear-gradient(160deg,#cfd4d8,#b69a3a 55%,#8a8f95)"></div>
  <div class="slide slide-main" style="left:340px;width:519px">
    <div role="img" aria-label="Foto von Braunglasflaschen auf einer Abfüllanlage" style="position:absolute;inset:0;background:linear-gradient(180deg,#3a3a3a 0%,#7a4a18 40%,#2a1a10 75%,#1a1a1a 100%)"></div>
    <div class="cap">
      <h3>Neue Abfüllanlage für<br>Sonnwald Limo</h3>
      <p>Der Traditionsreiche Limonadenhersteller Sonnwald Limo Aus Der Oberlausitz Investierte 2022/23 In Eine Neue Abfüllanlage. Federführend Beteiligt Bei Planung, Schnittstellenklärung Und Lieferung Der Anlage War Unser Unternehmen, In Zusammenarbeit Mit Weiteren Mittelständigen Firmen.</p>
    </div>
  </div>
  <div class="slide" role="img" aria-label="Foto einer Mitarbeiterin an einer Maschine" style="left:960px;width:240px;background:linear-gradient(160deg,#e6e6e2,#cfcfc8 50%,#a8a8a0)"></div>
  <svg class="arrow" style="left:283px" width="12" height="18" viewBox="0 0 12 18"><path d="M9 2 3 9l6 7" fill="none" stroke="#f07d1a" stroke-width="2.5"/></svg>
  <svg class="arrow" style="left:904px" width="12" height="18" viewBox="0 0 12 18"><path d="m3 2 6 7-6 7" fill="none" stroke="#f07d1a" stroke-width="2.5"/></svg>
</section>

<section class="abs jobs">
  <h2>JOBS / KARRIERE</h2>
  <div class="job" style="left:163px"><h4>SPS-Programmierung</h4><p>Lorem Ipsum Dolor Sit Amet, Consectetur Adipiscing Elit, Sed Do Eiusmod Tempor Incididunt Ut Labore Et Dolore Magna Aliqua. Ut Enim Ad Min</p><div class="btn btn-green">Bewerben</div></div>
  <div class="job" style="left:474px"><h4>SPS-Programmierung</h4><p>Lorem Ipsum Dolor Sit Amet, Consectetur Adipiscing Elit, Sed Do Eiusmod Tempor Incididunt Ut Labore Et Dolore Magna Aliqua. Ut Enim Ad Min</p><div class="btn btn-dark">Bewerben</div></div>
  <div class="job" style="left:784px"><h4>SPS-Programmierung</h4><p>Lorem Ipsum Dolor Sit Amet, Consectetur Adipiscing Elit, Sed Do Eiusmod Tempor Incididunt Ut Labore Et Dolore Magna Aliqua. Ut Enim Ad Min</p><div class="btn btn-dark">Bewerben</div></div>
</section>
<div class="abs person" role="img" aria-label="Foto eines Ingenieurs mit Schutzhelm"></div>

<section class="abs unternehmen">
  <h2 class="section-title" style="top:56px">UNTERNEHMEN</h2>
  <div class="logo-big">KOLMA Maschinenbau GmbH</div>
  <div class="copy">
    <p>Das Traditionsreiche Familienunternehmen Kolma Plant, Entwickelt Und Baut Pack- Und Palettieranlagen Für Den Getränke- Und Lebensmittelbereich. Mit Erfahrung Und Know-How Planen Und Konstruieren Wir Moderne Und Effiziente Anlagen, Die Optimal Auf Die Bedürfnisse Unserer Kunden Abgestimmt Sind.</p>
    <p>Wir Bieten Ihnen Individuelle Maschinen Und Anlagen Zur Abfüllung Und Verpackung, Sortier- Und Umpackanlagen Sowie Einen Umfassenden Rundum-Service An. Mit Unseren Weitläufigen Produktionsstätten Sind Wir In Der Lage, Die Vorarbeiten Der Montage Unter Unserem Dach Zu Erledigen, Sodass Der Zeitaufwand Für Den Aufbau Bei Ihnen Vor Ort Gering Ist.</p>
  </div>
  <div class="btn btn-dark">Mehr Erfahren</div>
</section>

<section class="abs kontakt">
  <h2>KONTAKT</h2>
  <div class="field" style="left:74px;top:112px"><label>Vorname</label><div class="input">Deine Vorname</div></div>
  <div class="field" style="left:284px;top:112px"><label>Nachname</label><div class="input">Deine Nachname</div></div>
  <div class="field" style="left:74px;top:169px"><label>Email</label><div class="input filled">info@kolmatech.de</div></div>
  <div class="field" style="left:284px;top:169px"><label>Telefonnummer</label><div class="input">Dein Telefonnummer</div></div>
  <div class="field" style="left:74px;top:232px;width:385px"><div class="input" style="height:82px">Schreibe deine Nachricht...</div></div>
  <div class="abs btn" style="left:74px;top:336px;width:145px;height:36px;background:var(--orange);gap:10px;font-weight:500">
    <svg width="14" height="14" viewBox="0 0 24 24"><path fill="#fff" d="M2 11 22 2l-9 20-2-9z"/></svg>Senden
  </div>
</section>
<div class="abs building" role="img" aria-label="Foto eines modernen Firmengebäudes"></div>

<footer class="abs footer">
  <div class="fcol" style="left:74px"><h5>KONTAKT</h5>KOLMA Maschinenbau GmbH<br>Am Werkhof 12<br>01234 Musterstadt</div>
  <div class="fcol" style="left:239px;top:53px">030 / 4567 - 0<br>030 / 4567 - 14<br>info@kolmatech.de</div>
  <div class="fcol" style="left:340px"><h5>QUICKLINKS</h5>Unternehmen<br>Jobs / Karriere<br>Palettiertechnik</div>
  <div class="fcol" style="left:429px;top:53px">Packertechnik<br>Fördertechnik<br>Anlagen</div>
  <div class="fcol" style="left:517px;top:53px">Gebrauchtmaschinen<br>Aktuelles</div>
  <div class="fcol" style="left:649px"><h5>PRODUKTE</h5>PALETTIERTECHNIK<br>PACKERTECHNIK</div>
  <div class="fcol" style="left:783px;top:53px">FÖRDERTECHNIK<br>GEBRAUCHTMASCHINEN</div>
  <div class="fcol" style="left:951px"><h5 style="font-size:9px">Abonnieren Sie den Newsletter</h5></div>
  <div class="abs" style="left:948px;top:84px;width:146px;height:26px;background:#fff;color:#888;font-size:9px;padding:8px 10px">Email</div>
  <div class="abs" style="left:1094px;top:84px;width:31px;height:26px;background:var(--green);display:flex;align-items:center;justify-content:center">
    <svg width="12" height="10" viewBox="0 0 12 10"><path d="M0 5h10M6 1l4 4-4 4" fill="none" stroke="#fff" stroke-width="1.6"/></svg>
  </div>
  <div class="copyright">©2024. KOLMA Maschinenbau GmbH All rights reserved</div>
</footer>

</body>
</html>
```